Exhibition Print

Need to have a few video meetings and work scope
we have approx 20 panels that need to tell a story of our business
I have updated a story board'
Our main company is:
vorlinet.com.au fibre to the home technologies for new or greenfield retirement estates and ethernet over copper for existing retirement estates

We will pay for the extra meetings on top

so the design needs approx 20 panels 2.4m HEIGHT x 1m WIDE
so we will work out the correct way to price this together

Target Market(s)

retirement communiites

Industry/Entity Type

retirement and communication technologies

Requirements
Nice to have
• i have attached a story board

```html
<!DOCTYPE html>
<html lang="en">
<head>
<meta charset="utf-8">
<title>Vorlinet Exhibition Panels</title>
<link href="https://fonts.googleapis.com/css2?family=Montserrat:wght@800;900&family=Open+Sans:wght@400;600;700&display=swap" rel="stylesheet">
<style>
  :root {
    --navy: #2e3b7c;
    --navy-deep: #243166;
    --grey-bg: #d9d9d9;
    --grey-dot: #c9c9c9;
    --ink: #2b2b2b;
    --white: #ffffff;
    --icon-bg: #e4e5ea;
  }
  * { box-sizing: border-box; margin: 0; padding: 0; }
  html, body { width: 1200px; height: 720px; overflow: hidden; }
  body {
    background: var(--grey-bg);
    font-family: "Open Sans", Arial, sans-serif;
    position: relative;
  }
  .panel {
    position: absolute;
    top: 55px;
    width: 257px;
    height: 610px;
    background: var(--white);
    box-shadow: 0 3px 8px rgba(0,0,0,0.28);
    overflow: hidden;
  }
  .panel--intro { left: 61px; border: 3px solid var(--white); }
  .panel--journey { left: 343px; }
  .panel--values { left: 626px; }
  .panel--fibre { left: 909px; }

  .panel-title {
    font-family: "Montserrat", Arial, sans-serif;
    font-weight: 900;
    font-size: 23.5px;
    line-height: 26px;
    text-align: center;
    color: var(--navy);
    letter-spacing: 0.3px;
    position: absolute;
    left: 0; right: 0;
    top: 18px;
  }

  /* Panel 1 */
  .intro-photo {
    position: absolute; inset: 0;
    background: linear-gradient(180deg, #4f5f9e 0%, #7d7fb6 22%, #a99cc4 40%, #c2a7c6 55%, #8a7ea8 68%, #3b3f63 82%, #1e2238 100%);
  }
  .panel--intro .panel-title { color: var(--white); top: 16px; }
  .intro-copy {
    position: absolute; top: 93px; left: 10px; right: 10px;
    color: var(--white); text-align: center;
    font-size: 13.2px; line-height: 16px;
  }

  /* Panel 2 */
  .journey-stats {
    position: absolute; top: 95px; left: 10px; right: 10px;
    text-align: center; font-size: 13.2px; line-height: 16px; color: var(--ink);
  }
  .journey-divider {
    position: absolute; top: 136px; left: 124px;
    width: 9px; height: 9px; background: var(--grey-dot); transform: rotate(45deg);
  }
  .mission-label {
    position: absolute; top: 153px; left: 0; right: 0; text-align: center;
    font-weight: 700; font-size: 14.5px; color: var(--navy); letter-spacing: 0.3px;
  }
  .mission-copy {
    position: absolute; top: 170px; left: 10px; right: 10px; text-align: center;
    font-size: 13.2px; line-height: 16px; color: var(--ink);
  }
  .timeline { position: absolute; top: 215px; left: 0; width: 257px; height: 390px; }
  .timeline text { font-family: "Open Sans", Arial, sans-serif; font-size: 3.6px; fill: #444; }

  /* Panels 3 & 4 */
  .feature-list { position: absolute; left: 0; right: 0; list-style: none; z-index: 2; }
  .feature-item { position: absolute; display: flex; align-items: center; }
  .feature-icon {
    width: 27px; height: 27px; border-radius: 50%;
    background: var(--icon-bg);
    display: flex; align-items: center; justify-content: center;
    flex-shrink: 0;
  }
  .feature-icon svg { width: 17px; height: 17px; }
  .feature-text { font-size: 11px; color: var(--ink); margin-left: 8px; letter-spacing: 0.2px; }
  .panel--values .feature-item { left: 17px; }
  .panel--fibre .feature-item { left: 21px; }
  .panel--fibre .feature-text { font-weight: 600; margin-left: 10px; }

  .values-photo {
    position: absolute; left: 3px; right: 3px; top: 173px; bottom: 3px;
    background: linear-gradient(180deg, rgba(255,255,255,1) 0%, #efe6da 12%, #e6d2b5 40%, #d8b98f 70%, #c59b6c 100%);
  }
  .fibre-subtitle {
    position: absolute; top: 72px; left: 0; right: 0; text-align: center;
    font-weight: 700; font-size: 20px; color: var(--ink);
  }
  .fibre-photo {
    position: absolute; left: 3px; right: 3px; top: 226px; bottom: 3px;
    background:
      linear-gradient(180deg, rgba(255,255,255,1) 0%, rgba(255,255,255,0) 14%),
      linear-gradient(115deg, #5b5fb4 0%, #7a7fcb 35%, #a89ad6 55%, #d9a86a 75%, #e7a04a 100%);
  }
</style>
</head>
<body>

<section class="panel panel--intro">
  <div class="intro-photo" role="img" aria-label="Photo of a smiling older couple looking at their phones outdoors at dusk under a purple sky"></div>
  <h2 class="panel-title">WE KEEP YOU<br>CONNECTED</h2>
  <p class="intro-copy">Vorlinet Health keeps retirement communities connected through future-ready telecom and care solutions.</p>
</section>

<section class="panel panel--journey">
  <h2 class="panel-title">OUR JOURNEY &amp;<br>MISSION</h2>
  <p class="journey-stats">20+ years, 40,000+ services, from 2004 to now.</p>
  <div class="journey-divider"></div>
  <p class="mission-label">MISSION:</p>
  <p class="mission-copy">Bridging distances, connecting hearts.</p>

  <svg class="timeline" viewBox="0 0 257 390" aria-label="Company milestones timeline">
    <defs>
      <marker id="arrow" viewBox="0 0 10 10" refX="5" refY="5" markerWidth="5" markerHeight="5" orient="auto">
        <path d="M1 1 L9 5 L1 9 Z" fill="none" stroke="#2e3b7c" stroke-width="1.2"/>
      </marker>
    </defs>
    <g fill="none" stroke="#2e3b7c" stroke-width="0.6" stroke-dasharray="2 1.5">
      <path d="M177 47 Q187 62 184 82" marker-end="url(#arrow)"/>
      <path d="M86 111 Q74 126 79 144" marker-end="url(#arrow)"/>
      <path d="M177 171 Q187 186 184 206" marker-end="url(#arrow)"/>
      <path d="M86 235 Q74 250 79 268" marker-end="url(#arrow)"/>
      <path d="M177 297 Q187 312 184 332" marker-end="url(#arrow)"/>
    </g>
    <!-- milestones -->
    <g>
      <circle cx="145" cy="35" r="31.5" fill="#fff" stroke="#2e3b7c" stroke-width="0.8"/>
      <circle cx="145" cy="35" r="26.5" fill="#2e3b7c"/>
      <rect x="62" y="11" width="43" height="9" rx="4.5" fill="#2e3b7c"/>
      <text x="63" y="25">2004: first retirement</text><text x="63" y="29.6">estate joins our network,</text><text x="63" y="34.2">with fibre and phone</text><text x="63" y="38.8">services installed</text>
    </g>
    <g>
      <circle cx="117" cy="96" r="31.5" fill="#fff" stroke="#2e3b7c" stroke-width="0.8" stroke-dasharray="2 1.5"/>
      <circle cx="117" cy="96" r="26.5" fill="#c9c9c9"/>
      <rect x="158" y="73" width="43" height="9" rx="4.5" fill="#c9c9c9"/>
      <text x="159" y="87">Ethernet over copper</text><text x="159" y="91.6">brings fast links to</text><text x="159" y="96.2">existing estates across</text><text x="159" y="100.8">the region</text>
    </g>
    <g>
      <circle cx="145" cy="159" r="31.5" fill="#fff" stroke="#2e3b7c" stroke-width="0.8"/>
      <circle cx="145" cy="159" r="26.5" fill="#2e3b7c"/>
      <rect x="62" y="135" width="43" height="9" rx="4.5" fill="#2e3b7c"/>
      <text x="63" y="149">Care call systems</text><text x="63" y="153.6">added so residents can</text><text x="63" y="158.2">reach help at any</text><text x="63" y="162.8">hour of the day</text>
    </g>
    <g>
      <circle cx="117" cy="220" r="31.5" fill="#fff" stroke="#2e3b7c" stroke-width="0.8" stroke-dasharray="2 1.5"/>
      <circle cx="117" cy="220" r="26.5" fill="#c9c9c9"/>
      <rect x="158" y="197" width="43" height="9" rx="4.5" fill="#c9c9c9"/>
      <text x="159" y="211">New greenfield estates</text><text x="159" y="215.6">built fibre-ready from</text><text x="159" y="220.2">day one</text>
    </g>
    <g>
      <circle cx="145" cy="284" r="31.5" fill="#fff" stroke="#2e3b7c" stroke-width="0.8"/>
      <circle cx="145" cy="284" r="26.5" fill="#2e3b7c"/>
      <rect x="62" y="260" width="43" height="9" rx="4.5" fill="#2e3b7c"/>
      <text x="63" y="274">Telehealth rolls out</text><text x="63" y="278.6">to residents in</text><text x="63" y="283.2">every community</text>
    </g>
    <g>
      <circle cx="117" cy="346" r="31.5" fill="#fff" stroke="#2e3b7c" stroke-width="0.8" stroke-dasharray="2 1.5"/>
      <circle cx="117" cy="346" r="26.5" fill="#c9c9c9"/>
      <rect x="158" y="322" width="43" height="9" rx="4.5" fill="#c9c9c9"/>
      <text x="159" y="336">Today: 40,000+</text><text x="159" y="340.6">services keeping</text><text x="159" y="345.2">people connected</text>
    </g>
  </svg>
</section>

<section class="panel panel--values">
  <div class="values-photo" role="img" aria-label="Photo of a male carer in white scrubs helping an older woman with a walking cane in a bright room"></div>
  <h2 class="panel-title">PEOPLE-CENTRIC<br>VALUES</h2>
  <ul class="feature-list">
    <li class="feature-item" style="top:73px">
      <span class="feature-icon"><svg viewBox="0 0 20 20" fill="none" stroke="#2e3b7c" stroke-width="1.2"><circle cx="9" cy="6" r="3"/><path d="M3 17c0-4 3-6 6-6s5 1 5.5 3"/><circle cx="15" cy="15" r="3"/><path d="M15 13.5V15h1.3"/></svg></span>
      <span class="feature-text">Dedication</span>
    </li>
    <li class="feature-item" style="top:107px">
      <span class="feature-icon"><svg viewBox="0 0 20 20" fill="none" stroke="#2e3b7c" stroke-width="1.2"><path d="M2 4h10v6H6l-3 2.5V10H2z"/><path d="M8 12v2h6l3 2.5V14h1V8h-4"/></svg></span>
      <span class="feature-text">Communication</span>
    </li>
    <li class="feature-item" style="top:141px">
      <span class="feature-icon"><svg viewBox="0 0 20 20"><path d="M10 17 3 10a4 4 0 0 1 7-5 4 4 0 0 1 7 5z" fill="#2e3b7c"/><circle cx="15" cy="14" r="3.3" fill="#fff" stroke="#2e3b7c" stroke-width="1"/><path d="M13.6 14l1 1 1.8-2" fill="none" stroke="#2e3b7c" stroke-width="1"/></svg></span>
      <span class="feature-text">Passion</span>
    </li>
    <li class="feature-item" style="top:175px">
      <span class="feature-icon"><svg viewBox="0 0 20 20" fill="none" stroke="#2e3b7c" stroke-width="1.1"><circle cx="7" cy="5" r="1.8"/><circle cx="13" cy="5" r="1.8"/><path d="M4 10c0-2 1.5-3 3-3s3 1 3 3M10 10c0-2 1.5-3 3-3s3 1 3 3"/><path d="M2 13h4l3 1.5h4l4-2.5v2l-5 3H7l-5-1z"/></svg></span>
      <span class="feature-text">Personalized local support.</span>
    </li>
  </ul>
</section>

<section class="panel panel--fibre">
  <div class="fibre-photo" role="img" aria-label="Photo of orange fibre optic cables plugged into network switch ports"></div>
  <h2 class="panel-title">HIGH-SPEED<br>CONNECTIVITY</h2>
  <p class="fibre-subtitle">Fibre to the Home</p>
  <ul class="feature-list">
    <li class="feature-item" style="top:104px">
      <span class="feature-icon"><svg viewBox="0 0 20 20" fill="none" stroke="#2e3b7c" stroke-width="1.2"><circle cx="11" cy="11" r="6"/><path d="M11 11l3-3M10 3h3M1 9h4M2 12h3M3 15h3"/></svg></span>
      <span class="feature-text">Fast, future-proof internet.</span>
    </li>
    <li class="feature-item" style="top:138px">
      <span class="feature-icon"><svg viewBox="0 0 20 20" fill="none" stroke="#2e3b7c" stroke-width="1.2"><circle cx="10" cy="10" r="7.5"/><rect x="5" y="7.5" width="6.5" height="5" rx="1"/><path d="M11.5 9.5l3-1.8v4.6l-3-1.8"/></svg></span>
      <span class="feature-text">Seamless video calls,</span>
    </li>
    <li class="feature-item" style="top:172px">
      <span class="feature-icon"><svg viewBox="0 0 20 20" fill="none" stroke="#2e3b7c" stroke-width="1.5"><circle cx="10" cy="10" r="1.4" fill="#2e3b7c"/><path d="M7 7a4 4 0 0 0 0 6M13 7a4 4 0 0 1 0 6M4.5 4.5a8 8 0 0 0 0 11M15.5 4.5a8 8 0 0 1 0 11"/></svg></span>
      <span class="feature-text">Streaming,</span>
    </li>
    <li class="feature-item" style="top:205px">
      <span class="feature-icon"><svg viewBox="0 0 20 20" fill="none" stroke="#2e3b7c" stroke-width="1.2"><rect x="4" y="4" width="12" height="9"/><path d="M2 15h16M7 11l2-3 2 2 1.5-1.5L14 11"/></svg></span>
      <span class="feature-text">Telehealth</span>
    </li>
  </ul>
</section>

</body>
</html>
```